Design a Brazilian children's Bible calendar for 2017

We need someone to design a children's calendar for 2017 with an animal theme.
The format is 21cm x 15cm and we need the front cover and one page with two months as can be seen in the attached files.
Target Market(s)
Brazilian children
Font styles to use
Sans Serif
Requirements
Must have
- Modern, clean design

```html
<!DOCTYPE html>
<html lang="pt-BR">
<head>
<meta charset="utf-8">
<title>Calendário Infantil 2017</title>
<link rel="stylesheet" href="https://fonts.googleapis.com/css2?family=Quicksand:wght@300;400;500;700&family=Raleway:wght@500;600;700&display=swap">
<style>
  :root {
    --bg: #ffffff;
    --coral: #e07862;
    --pink: #f29899;
    --mustard: #f6c453;
    --navy: #24496b;
    --plum: #3b2e3f;
    --rust: #9b3a1c;
    --sun: #f7e53a;
    --amber: #e8a23a;
    --white: #ffffff;
  }
  * { box-sizing: border-box; margin: 0; padding: 0; }
  html, body { width: 1200px; height: 480px; overflow: hidden; background: var(--bg); }
  .canvas { position: relative; width: 1200px; height: 480px; }

  .page {
    position: absolute; top: 16px; width: 318px; height: 446px;
    box-shadow: 3px 4px 8px rgba(0,0,0,0.28);
    overflow: hidden;
  }
  .page--jan { left: 54px; background: var(--coral); --title: var(--navy); --day: var(--navy); --verse: var(--navy); }
  .page--mar { left: 441px; background: var(--pink); --title: var(--sun); --day: var(--amber); --verse: var(--plum); }
  .page--mai { left: 822px; background: var(--mustard); --title: var(--rust); --day: var(--amber); --verse: var(--rust); }

  .photo { position: absolute; left: 0; top: 0; width: 318px; height: 194px; }
  .photo--puppy { background: linear-gradient(160deg, #6f6a55 0%, #cfc6bb 35%, #e5ddd3 70%, #c9beb1 100%); }
  .photo--cat { background: linear-gradient(160deg, #3a3a38 0%, #8c8a86 40%, #d8d4cf 60%, #5b5955 100%); }
  .photo--giraffe { background: linear-gradient(160deg, #b9c4b6 0%, #4d7a4a 35%, #3f6a3d 70%, #5b8450 100%); }

  .illustration { position: absolute; top: 208px; height: 62px; border-radius: 30px 30px 4px 4px; }
  .page--jan .illustration { left: 74px; width: 190px; background: linear-gradient(180deg, rgba(140,190,90,0) 0%, rgba(110,170,80,0.55) 100%); }
  .page--mar .illustration { left: 26px; width: 266px; background: linear-gradient(180deg, rgba(60,58,75,0.55) 0%, rgba(50,170,70,0.7) 100%); }
  .page--mai .illustration { left: 26px; width: 266px; background: linear-gradient(180deg, rgba(255,255,255,0.18) 0%, rgba(110,150,60,0.55) 100%); }

  .year {
    position: absolute; left: 0; right: 0; top: 246px; text-align: center;
    font: 700 25px/1 "Quicksand", sans-serif; color: var(--title); letter-spacing: 0.5px;
  }

  .verse {
    position: absolute; left: 10px; right: 10px; top: 288px; text-align: center;
    font: 600 10px/1 "Raleway", sans-serif; color: var(--verse);
  }
  .page--mar .verse, .page--mai .verse { top: 284px; line-height: 0.8; }
  .verse__ref {
    display: block; margin-top: 4px; font: 600 6px/1 "Raleway", sans-serif;
  }
  .page--mar .verse__ref, .page--mai .verse__ref { margin-top: 5px; font-size: 7px; }

  .month { position: absolute; top: 312px; width: 122px; }
  .month--first { left: 25px; }
  .month--second { left: 172px; }
  .month__name {
    text-align: center; font: 300 21px/1 "Quicksand", sans-serif; color: var(--white); height: 25px;
  }
  .weekdays, .dates {
    list-style: none; display: grid; grid-template-columns: repeat(7, 17.4px);
  }
  .weekdays { margin-top: 3px; }
  .weekdays li {
    width: 15px; height: 15px; border-radius: 50%; background: var(--white); margin: 0 auto;
    font: 700 4.6px/15px "Quicksand", sans-serif; color: var(--day); text-align: center;
  }
  .dates { margin-top: 4px; grid-auto-rows: 13.6px; }
  .dates li {
    text-align: center; font: 500 11px/13.6px "Quicksand", sans-serif; color: var(--white);
  }
  .start-sun { grid-column-start: 1; }
  .start-mon { grid-column-start: 2; }
  .start-wed { grid-column-start: 4; }
  .start-thu { grid-column-start: 5; }
  .start-sat { grid-column-start: 7; }
</style>
</head>
<body>
<main class="canvas">

  <!-- Janeiro / Fevereiro -->
  <section class="page page--jan">
    <div class="photo photo--puppy" role="img" aria-label="Fotografia de um filhote de cachorro preto e branco deitado na areia com uma bola colorida"></div>
    <div class="illustration" role="img" aria-label="Ilustração de grama, flores, borboleta e um cachorrinho com osso"></div>
    <div class="year">2017</div>
    <p class="verse">No principio, criou Deus os ceuse a terra<span class="verse__ref">Genesis 1 V 1</span></p>

    <div class="month month--first">
      <h2 class="month__name">Janeiro</h2>
      <ul class="weekdays"><li>DOM</li><li>TER</li><li>QUA</li><li>QUI</li><li>QUI</li><li>SEX</li><li>SÁB</li></ul>
      <ol class="dates">
        <li class="start-sun">1</li><li>2</li><li>3</li><li>4</li><li>5</li><li>6</li><li>7</li>
        <li>8</li><li>9</li><li>10</li><li>11</li><li>12</li><li>13</li><li>14</li>
        <li>15</li><li>16</li><li>17</li><li>18</li><li>19</li><li>20</li><li>21</li>
        <li>22</li><li>23</li><li>24</li><li>25</li><li>26</li><li>27</li><li>28</li>
        <li>29</li><li>30</li><li>31</li>
      </ol>
    </div>
    <div class="month month--second">
      <h2 class="month__name">Fevereiro</h2>
      <ul class="weekdays"><li>DOM</li><li>TER</li><li>QUA</li><li>QUI</li><li>QUI</li><li>SEX</li><li>SÁB</li></ul>
      <ol class="dates">
        <li class="start-thu">1</li><li>2</li><li>3</li><li>4</li>
        <li>5</li><li>6</li><li>7</li><li>8</li><li>9</li><li>10</li><li>11</li>
        <li>12</li><li>13</li><li>14</li><li>15</li><li>16</li><li>17</li><li>18</li>
        <li>19</li><li>20</li><li>21</li><li>22</li><li>23</li><li>24</li><li>25</li>
        <li>26</li><li>27</li><li>28</li>
      </ol>
    </div>
  </section>

  <!-- Março / Abril -->
  <section class="page page--mar">
    <div class="photo photo--cat" role="img" aria-label="Fotografia de um gato branco e malhado de olhos azuis deitado no chão"></div>
    <div class="illustration" role="img" aria-label="Ilustração noturna com gato marrom, arbustos verdes, nuvem escura e lua crescente"></div>
    <div class="year">2017</div>
    <p class="verse">Lorem ipsum dolor sit amet czonsectetuer adipiscing elit aenean commodo<span class="verse__ref">Lorem Ipsum</span></p>

    <div class="month month--first">
      <h2 class="month__name">Marco</h2>
      <ul class="weekdays"><li>DOM</li><li>TER</li><li>QUA</li><li>QUI</li><li>QUI</li><li>SEX</li><li>SÁB</li></ul>
      <ol class="dates">
        <li class="start-thu">1</li><li>2</li><li>3</li><li>4</li>
        <li>5</li><li>6</li><li>7</li><li>8</li><li>9</li><li>10</li><li>11</li>
        <li>12</li><li>13</li><li>14</li><li>15</li><li>16</li><li>17</li><li>18</li>
        <li>19</li><li>20</li><li>21</li><li>22</li><li>23</li><li>24</li><li>25</li>
        <li>26</li><li>27</li><li>28</li><li>29</li><li>30</li><li>31</li>
      </ol>
    </div>
    <div class="month month--second">
      <h2 class="month__name">Abril</h2>
      <ul class="weekdays"><li>DOM</li><li>TER</li><li>QUA</li><li>QUI</li><li>QUI</li><li>SEX</li><li>SÁB</li></ul>
      <ol class="dates">
        <li class="start-sun">1</li><li>2</li><li>3</li><li>4</li><li>5</li><li>6</li><li>7</li>
        <li>8</li><li>9</li><li>10</li><li>11</li><li>12</li><li>13</li><li>14</li>
        <li>15</li><li>16</li><li>17</li><li>18</li><li>19</li><li>20</li><li>21</li>
        <li>22</li><li>23</li><li>24</li><li>25</li><li>26</li><li>27</li><li>28</li>
        <li>29</li><li>30</li>
      </ol>
    </div>
  </section>

  <!-- Maio / Junho -->
  <section class="page page--mai">
    <div class="photo photo--giraffe" role="img" aria-label="Fotografia de uma girafa diante de árvores verdes"></div>
    <div class="illustration" role="img" aria-label="Ilustração de girafa laranja, arbustos verdes, nuvens contornadas e pássaros"></div>
    <div class="year">2017</div>
    <p class="verse">Lorem ipsum dolor sit amet czonsectetuer adipiscing elit aenean commodo<span class="verse__ref">Lorem Ipsum</span></p>

    <div class="month month--first">
      <h2 class="month__name">Maio</h2>
      <ul class="weekdays"><li>DOM</li><li>TER</li><li>QUA</li><li>QUI</li><li>QUI</li><li>SEX</li><li>SÁB</li></ul>
      <ol class="dates">
        <li class="start-mon">1</li><li>2</li><li>3</li><li>4</li><li>5</li><li>6</li>
        <li>7</li><li>8</li><li>9</li><li>10</li><li>11</li><li>12</li><li>13</li>
        <li>14</li><li>15</li><li>16</li><li>17</li><li>18</li><li>19</li><li>20</li>
        <li>21</li><li>22</li><li>23</li><li>24</li><li>25</li><li>26</li><li>27</li>
        <li>28</li><li>29</li><li>30</li><li>31</li>
      </ol>
    </div>
    <div class="month month--second">
      <h2 class="month__name">Junho</h2>
      <ul class="weekdays"><li>DOM</li><li>TER</li><li>QUA</li><li>QUI</li><li>QUI</li><li>SEX</li><li>SÁB</li></ul>
      <ol class="dates">
        <li class="start-wed">1</li><li>2</li><li>3</li>
        <li>4</li><li>5</li><li>6</li><li>7</li><li>8</li><li>9</li><li>10</li>
        <li>11</li><li>12</li><li>13</li><li>14</li><li>15</li><li>16</li><li>17</li>
        <li>18</li><li>19</li><li>20</li><li>21</li><li>22</li><li>23</li><li>24</li>
        <li>25</li><li>26</li><li>27</li><li>28</li><li>29</li><li>30</li>
      </ol>
    </div>
  </section>

</main>
</body>
</html>
```